New Business card design to reflect rebrand

I would like a business card design with a good base colour for our new logo and also a placeholder for a profile pic of the card holder. the design needs to be editable to the point that we can easily change the picture of the person and use that design for printmerlo etc. we are looking at a metalic finish business card so will need a good base colour to bring out the finish.

Target Market(s)

prospective customers

Industry/Entity Type

Business

Contact Information for Business Card

I would like one editable design that we can change the name of the card holder and profile picture. The design need to be in a format that be send to printmerlo etc.

Our address is Fenwick Lodge, Copse Lane, Hartley Wintney, GU14 3TP Tel no. 01483 556172

Requirements
Must have
• place holder for a profile pic for the card holder. in AI or preferably PSD format

```html
<!DOCTYPE html>
<html lang="en">
<head>
<meta charset="utf-8">
<title>Norvale Workplace Services – Business Card</title>
<link rel="stylesheet" href="https://fonts.googleapis.com/css2?family=Lato:wght@400;700;900&display=swap">
<style>
  :root {
    --navy: #3f5572;
    --orange: #ea6409;
    --white: #ffffff;
    --paper: #e9ebee;
    --shadow: rgba(20, 30, 45, 0.18);
  }
  * { margin: 0; padding: 0; box-sizing: border-box; }
  html, body { width: 1200px; height: 1200px; overflow: hidden; }
  body {
    background: var(--paper);
    font-family: "Lato", sans-serif;
    position: relative;
  }
  .card {
    position: absolute;
    left: 160px;
    width: 880px;
    height: 503px;
    background: var(--white);
    box-shadow: 0 6px 22px var(--shadow);
    overflow: hidden;
  }
  .card--back { top: 62px; }
  .card--front { top: 635px; }

  /* Shared brand lockup */
  .brand {
    position: absolute; display: flex; flex-direction: column; align-items: center;
    color: var(--navy); font-weight: 900; text-transform: uppercase; line-height: 1;
  }
  .brand__mark { background: var(--navy); }
  .brand__name { letter-spacing: 4px; }
  .brand__tag { color: var(--navy); letter-spacing: 5px; }

  /* Back */
  .back__top-band { position: absolute; left: 0; top: 0; width: 100%; height: 107px; background: var(--navy); }
  .back__bottom-band {
    position: absolute; left: 0; bottom: 0; width: 100%; height: 105px; background: var(--orange);
    display: flex; align-items: center; justify-content: center;
  }
  .back__web { color: var(--white); font-weight: 700; font-size: 25px; letter-spacing: 6px; }
  .card--back .brand { left: 0; width: 100%; top: 168px; }
  .card--back .brand__mark { width: 40px; height: 40px; margin-bottom: 36px; }
  .card--back .brand__name { font-size: 68px; letter-spacing: 6px; }
  .card--back .brand__tag { font-size: 26px; margin-top: 14px; letter-spacing: 6px; }

  /* Front */
  .front__band { position: absolute; left: 0; top: 273px; width: 100%; height: 73px; background: var(--navy); }
  .front__base { position: absolute; left: 0; top: 346px; width: 100%; height: 157px; background: var(--orange); }
  .front__photo {
    position: absolute; left: 24px; top: 92px; width: 268px; height: 411px;
    background: linear-gradient(180deg, #d9b48f 0%, #c9a07c 32%, #2a2c31 60%, #16171a 100%);
    border-radius: 120px 120px 0 0;
  }
  .card--front .brand { left: 370px; width: 420px; top: 70px; }
  .card--front .brand__mark { width: 28px; height: 28px; margin-bottom: 20px; }
  .card--front .brand__name { font-size: 50px; letter-spacing: 5px; }
  .card--front .brand__tag { font-size: 18px; margin-top: 9px; }
  .front__address {
    position: absolute; left: 343px; top: 222px; display: flex; align-items: center; gap: 14px;
    color: var(--navy); font-size: 16px;
  }
  .front__holder {
    position: absolute; left: 319px; top: 273px; height: 73px; display: flex; align-items: center; gap: 18px;
  }
  .holder__name { color: var(--white); font-size: 27px; font-weight: 700; }
  .holder__title { color: var(--orange); font-size: 19px; }
  .contact {
    position: absolute; display: flex; align-items: center; gap: 18px;
    color: var(--white); font-size: 19px;
  }
  .icon-badge {
    width: 28px; height: 28px; border-radius: 6px; background: var(--navy);
    display: flex; align-items: center; justify-content: center; flex: none;
  }
  .icon-pin {
    width: 28px; height: 28px; border-radius: 6px; background: var(--orange);
    display: flex; align-items: center; justify-content: center; flex: none;
  }
</style>
</head>
<body>

  <section class="card card--back" aria-label="Card back">
    <div class="back__top-band"></div>
    <div class="brand">
      <span class="brand__mark"></span>
      <span class="brand__name">Norvale</span>
      <span class="brand__tag">Workplace Services</span>
    </div>
    <div class="back__bottom-band"><span class="back__web">www.website.com</span></div>
  </section>

  <section class="card card--front" aria-label="Card front">
    <div class="front__band"></div>
    <div class="front__base"></div>
    <div class="front__photo" role="img" aria-label="Profile photo of the card holder"></div>

    <div class="brand">
      <span class="brand__mark"></span>
      <span class="brand__name">Norvale</span>
      <span class="brand__tag">Workplace Services</span>
    </div>

    <div class="front__address">
      <span class="icon-pin">
        <svg width="16" height="18" viewBox="0 0 16 18"><path d="M8 1a6 6 0 0 0-6 6c0 4.5 6 10 6 10s6-5.5 6-10a6 6 0 0 0-6-6z" fill="#fff"/><circle cx="8" cy="7" r="2.3" fill="#ea6409"/></svg>
      </span>
      <span>Address: Street No, Nord Avenue, Co,City/State Zipcode</span>
    </div>

    <div class="front__holder">
      <span class="holder__name">CARD HOLDER NAME</span>
      <span class="holder__title">JOB TITLE</span>
    </div>

    <div class="contact" style="left:374px; top:388px;">
      <span class="icon-badge"><svg width="14" height="18" viewBox="0 0 14 18"><rect x="2" y="1" width="10" height="16" rx="2" fill="none" stroke="#fff" stroke-width="1.8"/><circle cx="7" cy="14" r="1" fill="#fff"/></svg></span>
      <span>+ 000 - 000 - 000</span>
    </div>
    <div class="contact" style="left:374px; top:436px;">
      <span class="icon-badge"><svg width="16" height="16" viewBox="0 0 16 16"><path d="M4 1.5l2.2 3-1.4 1.6c.8 1.9 2.2 3.3 4.1 4.1l1.6-1.4 3 2.2-1.3 2.5C7 13.2 2.8 9 2.5 2.8z" fill="#fff"/></svg></span>
      <span>+ 000 - 000 - 000</span>
    </div>
    <div class="contact" style="left:610px; top:388px;">
      <span class="icon-badge"><svg width="18" height="14" viewBox="0 0 18 14"><rect x="1.5" y="1.5" width="15" height="11" rx="1.5" fill="none" stroke="#fff" stroke-width="1.6"/><path d="M2 2.5l7 5.5 7-5.5" fill="none" stroke="#fff" stroke-width="1.6"/></svg></span>
      <span>mail@website.com</span>
    </div>
    <div class="contact" style="left:610px; top:436px;">
      <span class="icon-badge"><svg width="18" height="18" viewBox="0 0 18 18" fill="none" stroke="#fff" stroke-width="1.4"><circle cx="9" cy="9" r="7"/><ellipse cx="9" cy="9" rx="3" ry="7"/><path d="M2 9h14M3 5.5h12M3 12.5h12"/></svg></span>
      <span>www.website.com</span>
    </div>
  </section>

</body>
</html>
```